FunBrixo Business Card

We need a business card design for our company. We sell construction-themed amusement rides for kids.

Contact Information for Business Card

Contact info on business card should include:
Carl Dunning
Co-Founder & COO
(833) 571-FUNBRIX
Carl@funbrixo-demo.com
www.funbrixo-demo.com

```html
<!DOCTYPE html>
<html lang="en">
<head>
<meta charset="utf-8">
<title>FunBrixo Business Card</title>
<link rel="stylesheet" href="https://fonts.googleapis.com/css2?family=Russo+One&family=Ubuntu:wght@300;400;700&display=swap">
<style>
  :root {
    --backdrop: #2a2a2a;
    --card-white: #ffffff;
    --card-black: #0c0c0c;
    --brand-orange: #ef5a24;
    --accent-orange: #f39a1e;
    --accent-blue: #1fa6e0;
    --rule-dark: #1a1a1a;
    --ghost-brown: #2b1c14;
  }
  * { box-sizing: border-box; margin: 0; padding: 0; }
  html, body {
    width: 1200px; height: 900px; overflow: hidden;
    background: var(--backdrop);
  }
  .canvas {
    position: relative; width: 1200px; height: 900px;
  }
  .card {
    position: absolute; left: 240px; width: 720px; height: 400px;
    overflow: hidden;
    box-shadow: 0 10px 30px rgba(0,0,0,.5);
  }
  /* back side */
  .card-back { top: 40px; background: var(--card-black); }
  .ghost-name {
    position: absolute; left: 30px; top: 110px;
    font-family: "Ubuntu", sans-serif; font-weight: 700;
    font-size: 190px; line-height: 1; color: var(--ghost-brown);
    letter-spacing: -2px;
  }
  .crew-illustration {
    position: absolute; left: 210px; top: 50px; width: 340px; height: 330px;
    border-radius: 10px;
    background: linear-gradient(180deg, #f2c419 0%, #f2c419 18%, #e9b79a 30%, #d9531e 55%, #233a7a 80%, #555 100%);
    opacity: .9;
  }
  /* front side */
  .card-front { top: 460px; background: var(--card-white); }
  .brand-name {
    position: absolute; left: 70px; top: 50px;
    font-family: "Ubuntu", sans-serif; font-weight: 700;
    font-size: 88px; line-height: 1; color: var(--brand-orange);
  }
  .side-tab {
    position: absolute; left: 0; top: 182px; width: 9px; height: 46px;
    background: var(--accent-blue);
  }
  .person-name {
    position: absolute; left: 70px; top: 176px;
    font-family: "Russo One", sans-serif; font-size: 36px;
    color: var(--brand-orange);
  }
  .person-title {
    position: absolute; left: 70px; top: 222px;
    font-family: "Ubuntu", sans-serif; font-weight: 300; font-size: 21px;
    color: var(--accent-orange);
  }
  .divider {
    position: absolute; left: 70px; top: 268px; width: 600px; height: 2px;
    background: var(--rule-dark);
  }
  .contact-list {
    position: absolute; left: 70px; top: 286px; list-style: none;
    font-family: "Ubuntu", sans-serif; font-size: 21px; color: var(--accent-orange);
  }
  .contact-list li { display: flex; align-items: center; gap: 10px; height: 32px; }
  .contact-list svg { width: 20px; height: 20px; flex: none; }
  .contact-list strong { font-weight: 700; }
</style>
</head>
<body>
<main class="canvas">
  <section class="card card-back" aria-label="Card back">
    <div class="ghost-name" aria-hidden="true">FunBrixo</div>
    <div class="crew-illustration" role="img" aria-label="Cartoon illustration of two construction workers in yellow hard hats, one in overalls with a tool belt, one in a safety vest and tie"></div>
  </section>

  <section class="card card-front" aria-label="Card front">
    <div class="brand-name">FunBrixo</div>
    <div class="side-tab"></div>
    <h1 class="person-name">Carl Dunning</h1>
    <p class="person-title">Co-Founder &amp; COO</p>
    <div class="divider"></div>
    <ul class="contact-list">
      <li>
        <svg viewBox="0 0 24 24" fill="none" stroke="currentColor" stroke-width="2"><path d="M5 4h4l2 5-3 2a11 11 0 0 0 5 5l2-3 5 2v4a2 2 0 0 1-2 2A17 17 0 0 1 3 6a2 2 0 0 1 2-2z"/></svg>
        (833) 571-FUNBRIX
      </li>
      <li>
        <svg viewBox="0 0 24 24" fill="none" stroke="currentColor" stroke-width="2"><rect x="3" y="5" width="18" height="14"/><path d="M3 5l9 8 9-8"/></svg>
        Carl@funbrixo-demo.com
      </li>
      <li>
        <svg viewBox="0 0 24 24" fill="none" stroke="currentColor" stroke-width="2"><circle cx="12" cy="12" r="9"/><path d="M3 12h18M12 3c3 3 3 15 0 18M12 3c-3 3-3 15 0 18"/></svg>
        <span>www.<strong>funbrixo-demo</strong>.com</span>
      </li>
    </ul>
  </section>
</main>
</body>
</html>
```